We’re a real estate firm that has landed a big builder in a neighboring state. Our branding needs...

We are a real estate firm who represents various builders along with doing resale here in Oregon. Our firm is growing to represent a big builder in Washington State and we’ll have another 40 brokers on our team. We need rebranding. As in, a new logo ( the house logo we have now looks cartoonish, hate it). We need new cards, something to really stand out. I’ve been thinking of using those NFC cards from ZEP or the ones with the seam color. I likely want two or three designs, a darker (as in a background color of black or grey) , a light one ( again I mean background color) and a credit card style (either plastic w an embossed name/number on front, or metal ). I’m thinking dark background for cc, or silver if it’s metal. That’s my thoughts, but you are the artists, so maybe you have an idea I haven’t considered. Our colors were black and red, but we don’t have to stick to that. Just nothing too busy. Oh, and we are typically representing the local, higher quality builders in our area (just below custom), but not national. Subdivisions are near the Kell Varney, Brisco, and Thornfield Crest sites. We are super excited, but without a lot of time to change the “look” of our brokerage. So I’ll be deciding and moving forward within 24 hours tops. Our name is Real Estate Summit Alliance ( we cant change the name because of timeline and business license) Thank you!

Industry/Entity Type

Real Estate

Contact Information for Business Card

The usual. Name of firm. Name of cardholder. Contact info.

Font styles to use
Serif
Sans Serif

Colors

Designer to choose colors to be used in the design.

Requirements
Must have
• A sleek or simple look. I included photos of cards with stylistic attributes we like. Thank you
Nice to have
• We really like the black backgrounds. With foil or embossed detail. We also like the black on black. Matte black card with raised shiny black detail. But still eye catching.
Should not have
• No ornate or busy looking style. We don’t want anything cluttered.

```html
<!DOCTYPE html>
<html lang="en">
<head>
<meta charset="utf-8">
<title>Real Estate Summit Alliance – Business Card</title>
<link rel="stylesheet" href="https://fonts.googleapis.com/css2?family=Arimo:wght@400;700&family=Lato:wght@700;900&display=swap">
<style>
  :root {
    --backdrop: #8a5a33;
    --card-light: #dcbb93;
    --card-mid: #c79e70;
    --card-dark: #b4875a;
    --ink: #111111;
    --shadow: rgba(0, 0, 0, 0.45);
  }
  * { margin: 0; padding: 0; box-sizing: border-box; }
  html, body {
    width: 1200px;
    height: 900px;
    overflow: hidden;
    background: var(--backdrop);
  }
  .stage {
    position: relative;
    width: 1200px;
    height: 900px;
  }
  .card {
    position: absolute;
    left: 330px;
    width: 556px;
    height: 343px;
    background: linear-gradient(125deg, var(--card-light) 0%, var(--card-mid) 45%, var(--card-dark) 100%);
    box-shadow: 3px 4px 8px var(--shadow);
    color: var(--ink);
    text-align: center;
  }
  .card--back { top: 90px; }
  .card--front { top: 470px; width: 558px; }

  .holder-name {
    position: absolute;
    top: 62px;
    width: 100%;
    font-family: "Lato", sans-serif;
    font-weight: 700;
    font-size: 19px;
    letter-spacing: 0.2px;
  }
  .holder-title {
    position: absolute;
    top: 86px;
    width: 100%;
    font-family: "Arimo", sans-serif;
    font-size: 15.5px;
  }
  .rule {
    position: absolute;
    left: 180px;
    width: 196px;
    height: 1px;
    background: var(--ink);
  }
  .rule--top { top: 116px; }
  .rule--bottom { top: 222px; }

  .contact-list {
    position: absolute;
    top: 129px;
    width: 100%;
    list-style: none;
    font-family: "Arimo", sans-serif;
    font-size: 15.5px;
    line-height: 20.3px;
  }
  .contact-list b { font-weight: 700; }

  .address {
    position: absolute;
    top: 239px;
    width: 100%;
    font-family: "Arimo", sans-serif;
    font-size: 15.5px;
    line-height: 20px;
    font-style: normal;
  }

  .brand {
    position: absolute;
    top: 108px;
    left: 0;
    width: 100%;
    display: flex;
    justify-content: center;
    align-items: center;
    gap: 16px;
  }
  .brand-mark {
    width: 34px;
    height: 34px;
    background: var(--ink);
    flex: none;
  }
  .brand-name {
    font-family: "Lato", sans-serif;
    font-weight: 900;
    font-size: 34px;
    line-height: 40px;
    letter-spacing: 2px;
    text-transform: uppercase;
    text-align: left;
  }
</style>
</head>
<body>
  <main class="stage">
    <section class="card card--back" aria-label="Card back with contact details">
      <h1 class="holder-name">MARCUS ELLERY</h1>
      <p class="holder-title">Managing Director</p>
      <div class="rule rule--top"></div>
      <ul class="contact-list">
        <li><b>P:</b> 044-123 456 789</li>
        <li><b>M:</b> 044-123 456 789</li>
        <li><b>E:</b> info@webname.com</li>
        <li><b>W:</b> www.websitename.com</li>
      </ul>
      <div class="rule rule--bottom"></div>
      <address class="address">12345, Address Goes Here<br>Country Name, 123456.</address>
    </section>

    <section class="card card--front" aria-label="Card front with firm name">
      <div class="brand">
        <span class="brand-mark"></span>
        <span class="brand-name">Real Estate<br>Summit Alliance</span>
      </div>
    </section>
  </main>
</body>
</html>
```